Elegant Lumocrest Rentals DL flyer

We run a Lumocrest Rentals business - this will be used as a business card as well.

our website is lumocrestrentals.com.au

Front page it sour logo which is attached website details - on the front it needs to say wedding and event hire needs etc..

on the back we will have a spot for 4 products but we want to say there is more so check our the website

A background in the flyer only for example like this would be good http://tapestrova.com/dark-backdrop-image_4726.html

Wedding

Must have
• nice background elegant in style pink and black is the colours

```html
<!DOCTYPE html>
<html lang="en">
<head>
<meta charset="utf-8">
<title>Lumocrest Rentals – DL Flyer</title>
<link rel="stylesheet" href="https://fonts.googleapis.com/css2?family=Raleway:ital,wght@0,400;0,600;0,700;1,400&family=Roboto:wght@700&display=swap">
<style>
  :root {
    --stage: #4a4a4a;
    --paper: #ffffff;
    --paper-soft: #eeeeee;
    --pink: #e0238a;
    --pink-deep: #b8126b;
    --plum-dark: #1c0712;
    --ink: #111111;
    --grey-text: #555555;
    --logo-grey: #6b6b6b;
  }
  * { box-sizing: border-box; margin: 0; padding: 0; }
  html, body { width: 1200px; height: 1000px; overflow: hidden; }
  body { background: var(--stage); font-family: "Raleway", Arial, sans-serif; position: relative; }

  .flyer-side {
    position: absolute; left: 150px; width: 903px;
    background: linear-gradient(180deg, var(--paper) 0%, var(--paper-soft) 100%);
    box-shadow: 0 2px 6px rgba(0,0,0,.5);
    overflow: hidden;
  }
  .flyer-front { top: 53px; height: 428px; }
  .flyer-back { top: 516px; height: 427px; }
  .side-art { position: absolute; inset: 0; }

  .band-copy {
    position: absolute; color: #fff; font-style: italic; font-size: 18px; line-height: 25.5px;
  }
  .band-copy--left { right: 643px; top: 90px; text-align: right; }
  .band-copy--right { left: 665px; top: 87px; }

  .logo-card {
    position: absolute; left: 285px; top: 2px; width: 355px; height: 255px;
    background: var(--paper);
    box-shadow: 0 3px 8px rgba(0,0,0,.45);
    display: flex; flex-direction: column; align-items: center; justify-content: center; gap: 18px;
  }
  .logo-dot { width: 98px; height: 98px; border-radius: 50%; background: var(--pink); }
  .logo-name { font-weight: 600; font-size: 34px; color: var(--logo-grey); }

  .phone-tag {
    position: absolute; left: 327px; width: 271px; height: 51px;
    background: linear-gradient(180deg, var(--pink) 0%, var(--pink-deep) 100%);
    color: #fff; font-family: "Roboto", Arial, sans-serif; font-weight: 700; font-size: 40px;
    display: flex; align-items: center; justify-content: center;
    box-shadow: 0 2px 4px rgba(0,0,0,.4);
  }
  .web-line {
    position: absolute; left: 0; width: 903px; text-align: center;
    color: var(--pink); font-weight: 700; font-size: 22px;
  }
  .mail-line {
    position: absolute; left: 0; width: 903px; text-align: center;
    color: var(--pink); font-size: 17px;
  }
  .flyer-front .phone-tag { top: 279px; }
  .flyer-front .web-line { top: 344px; }
  .flyer-front .mail-line { top: 370px; }

  .products-title { position: absolute; left: 98px; top: 43px; font-size: 27px; color: var(--grey-text); }
  .product { position: absolute; top: 96px; text-align: center; }
  .product-name { color: #fff; font-size: 19px; display: block; height: 28px; }
  .product-photo { display: block; border: 1px solid #ddd; }
  .product--cocktail { left: 22px; width: 222px; }
  .product--cocktail .product-photo { width: 222px; height: 123px; background: linear-gradient(160deg, #8d8d8d, #4a4a4a); }
  .product--chairs { left: 256px; width: 174px; }
  .product--chairs .product-photo { width: 126px; height: 125px; margin: 0 auto; background: linear-gradient(180deg, #fafafa, #e6e6e6); }
  .product--antique { left: 443px; width: 218px; }
  .product--antique .product-photo { width: 218px; height: 121px; background: linear-gradient(180deg, #5d6b4a 0%, #d8d8d0 45%, #3f5a22 100%); }
  .product--cubes { left: 682px; width: 189px; }
  .product--cubes .product-photo { width: 189px; height: 122px; background: linear-gradient(135deg, #2a1030 0%, #3fbfa0 35%, #e0304a 65%, #9b3ad8 100%); }

  .back-logo-card {
    position: absolute; left: 47px; top: 279px; width: 221px; height: 148px;
    background: var(--paper); box-shadow: 0 2px 6px rgba(0,0,0,.4);
    display: flex; flex-direction: column; align-items: center; justify-content: center; gap: 10px;
  }
  .back-logo-card .logo-dot { width: 58px; height: 58px; }
  .back-logo-card .logo-name { font-size: 21px; }

  .flyer-back .phone-tag { top: 280px; }
  .flyer-back .web-line { top: 342px; }
  .flyer-back .mail-line { top: 368px; }

  .more-panel {
    position: absolute; left: 654px; top: 279px; width: 209px; height: 148px;
    background: linear-gradient(180deg, #3a3a3a, #111);
    box-shadow: 0 0 8px rgba(0,0,0,.6);
  }
  .more-arrow { position: absolute; left: 14px; top: 18px; }
  .more-text {
    position: absolute; left: 44px; top: 18px; width: 155px; text-align: center;
    color: var(--pink); font-weight: 700; font-size: 25px; line-height: 31px;
  }
</style>
</head>
<body>

<section class="flyer-side flyer-front">
  <svg class="side-art" viewBox="0 0 903 428" width="903" height="428" aria-hidden="true">
    <defs>
      <linearGradient id="bandFill" x1="0" y1="0" x2="0" y2="1">
        <stop offset="0" stop-color="#d81f82"/>
        <stop offset="0.55" stop-color="#6e0c40"/>
        <stop offset="1" stop-color="#1c0712"/>
      </linearGradient>
      <linearGradient id="baseFill" x1="0" y1="0" x2="0" y2="1">
        <stop offset="0" stop-color="#1a1a1a"/>
        <stop offset="1" stop-color="#050505"/>
      </linearGradient>
    </defs>
    <polygon points="0,84 285,84 285,217 0,253" fill="url(#bandFill)"/>
    <polygon points="640,74 900,47 900,225 640,225" fill="url(#bandFill)"/>
    <path d="M0,333 Q450,285 903,322 L903,428 L0,428 Z" fill="#e0238a"/>
    <path d="M0,343 Q450,298 903,340 L903,428 L0,428 Z" fill="url(#baseFill)"/>
  </svg>

  <p class="band-copy band-copy--left">A range of<br>Wedding packages<br>and equipment<br>to make your day special<br>without the extra cost.</p>
  <p class="band-copy band-copy--right">A range of party<br>products from cocktail<br>tables, cocktail stools,<br>glow products and more<br>to set your party alight.</p>

  <div class="logo-card">
    <span class="logo-dot"></span>
    <span class="logo-name">Lumocrest Rentals</span>
  </div>

  <div class="phone-tag">0412550386</div>
  <p class="web-line">lumocrestrentals.com.au</p>
  <p class="mail-line">info@lumocrestrentals.com.au</p>
</section>

<section class="flyer-side flyer-back">
  <svg class="side-art" viewBox="0 0 903 427" width="903" height="427" aria-hidden="true">
    <defs>
      <linearGradient id="showcaseFill" x1="0" y1="0" x2="0" y2="1">
        <stop offset="0" stop-color="#0d0d0d"/>
        <stop offset="0.6" stop-color="#555"/>
        <stop offset="1" stop-color="#e4e4e4"/>
      </linearGradient>
      <linearGradient id="footFill" x1="0" y1="0" x2="0" y2="1">
        <stop offset="0" stop-color="#1a1a1a"/>
        <stop offset="1" stop-color="#050505"/>
      </linearGradient>
    </defs>
    <polygon points="0,88 903,57 903,258 0,258" fill="url(#showcaseFill)"/>
    <path d="M0,330 Q450,282 903,305 L903,427 L0,427 Z" fill="#e0238a"/>
    <path d="M0,340 Q450,295 903,318 L903,427 L0,427 Z" fill="url(#footFill)"/>
  </svg>

  <h2 class="products-title">Some of our products:</h2>

  <figure class="product product--cocktail">
    <figcaption class="product-name">Cocktail Tables</figcaption>
    <span class="product-photo" role="img" aria-label="Photo of black cocktail tables with stools"></span>
  </figure>
  <figure class="product product--chairs">
    <figcaption class="product-name">Americana Chairs</figcaption>
    <span class="product-photo" role="img" aria-label="Photo of a white folding Americana chair"></span>
  </figure>
  <figure class="product product--antique">
    <figcaption class="product-name">Antique Tables</figcaption>
    <span class="product-photo" role="img" aria-label="Photo of a white antique table on grass"></span>
  </figure>
  <figure class="product product--cubes">
    <figcaption class="product-name">Glow Cubes</figcaption>
    <span class="product-photo" role="img" aria-label="Photo of colourful glowing LED cubes"></span>
  </figure>

  <div class="back-logo-card">
    <span class="logo-dot"></span>
    <span class="logo-name">Lumocrest Rentals</span>
  </div>

  <div class="phone-tag">0412550386</div>
  <p class="web-line">lumocrestrentals.com.au</p>
  <p class="mail-line">info@lumocrestrentals.com.au</p>

  <div class="more-panel">
    <svg class="more-arrow" width="30" height="100" viewBox="0 0 30 100" aria-hidden="true">
      <polygon points="30,0 30,100 0,50" fill="#e0238a"/>
    </svg>
    <p class="more-text">Check<br>our website<br>for more !</p>
  </div>
</section>

</body>
</html>
```